Construction proffessionals servicing the inner suburbs of Melbournes NorthWest specialising in aler

I would like a web site that is sharp, contemporary and simple to navigate, ie.not too many pages. i would like a home page with some info about us, who we are what our history is and my passion for building and construction based on impeccable customer focus. i would like a projects page and somewhere for clients to add testimonials. i would like a project calculator as well so prospective clients can work out a rough budget prior to contacting. i would like the colours to be in line with my logo which i have uploaded. i have many photos which can be used and can be shared via drop box when required. I would like it to be personal to capture our transparent process. i would like to add our company process as well. be brave and take risks.

Target Market(s)

People renovating and extending their homes, people needing inspections on new homes and pre-purchase inspections

Industry/Entity Type

Construction

Number of Pages Required

5+ page

Requirements
Must have
• Professional, easy to navigate, provide viewers with a happy experience, look great, contacts, project calculator, link through to my training company www.qdmn.learnhub.example also check rowenhq on instagram for pics
Nice to have
• Links to instagram, fonts to match email signature

```html
<!DOCTYPE html>
<html lang="en">
<head>
<meta charset="utf-8">
<title>Rowen Build – Home</title>
<link href="https://fonts.googleapis.com/css2?family=Open+Sans:wght@300;400;600;700&display=swap" rel="stylesheet">
<style>
  :root{
    --orange:#f7941d;
    --orange-light:#fbb040;
    --orange-deep:#f26f21;
    --ink:#3d3d3d;
    --grey:#777;
    --line:#e2e2e2;
    --footer:#3a3a3a;
    --white:#fff;
  }
  *{box-sizing:border-box;margin:0;padding:0}
  html,body{width:744px;height:1200px;overflow:hidden}
  body{font-family:"Open Sans",Arial,sans-serif;color:var(--ink);background:var(--white);position:relative}

  .site-header{position:absolute;left:0;top:0;width:744px;height:200px;
    background:linear-gradient(180deg,var(--orange-deep) 0%,var(--orange) 45%,var(--orange-light) 100%)}
  .brand{position:absolute;left:26px;top:12px;display:flex;align-items:center;gap:6px;
    font-weight:700;font-size:17px;color:var(--white)}
  .brand-mark{width:14px;height:14px;background:var(--white)}
  .contact-line{position:absolute;right:70px;top:24px;font-size:8px;color:var(--white)}
  .main-nav{position:absolute;right:70px;top:48px;display:flex;gap:20px}
  .main-nav a{font-size:8px;color:var(--white);text-decoration:none;font-weight:600}

  .hero{position:absolute;left:62px;top:95px;width:612px;height:270px;
    background:linear-gradient(135deg,#d9a27a 0%,#b37955 40%,#e8d6c2 70%,#8a5a3b 100%);
    box-shadow:0 2px 6px rgba(0,0,0,.25)}
  .hero-caption{position:absolute;left:0;bottom:0;width:100%;height:62px;background:rgba(20,20,20,.72);
    padding:10px 18px;color:var(--white)}
  .hero-caption h2{font-size:17px;font-weight:600}
  .hero-caption p{font-size:7.5px;margin-top:5px;color:#ddd}
  .hero-arrow{position:absolute;top:120px;width:16px;height:26px;background:rgba(0,0,0,.6)}
  .hero-arrow.prev{left:0}.hero-arrow.next{right:0}
  .hero-arrow svg{display:block;margin:7px auto}

  .about{position:absolute;left:62px;top:405px;width:612px;height:210px}
  .section-title{font-weight:300;color:var(--orange);font-size:19px}
  .about .section-title{position:absolute;left:0;top:0}
  .about-photo{position:absolute;left:0;top:40px;width:170px;height:150px;
    background:linear-gradient(135deg,#c89b68,#8c6a49 55%,#d8c6ad)}
  .about-text{position:absolute;left:185px;top:38px;width:235px;font-size:6.8px;line-height:1.55;color:var(--grey)}
  .about-text p+p{margin-top:8px}
  .btn{display:inline-block;background:var(--orange);color:var(--white);font-size:7px;font-weight:600;
    padding:6px 10px;border-radius:2px;white-space:nowrap}
  .read-more{position:absolute;left:187px;top:170px}

  .calculator{position:absolute;left:442px;top:0;width:170px;height:200px;border:1px solid var(--line);
    background:#fafafa;padding:12px 12px}
  .calculator h3{font-weight:400;color:var(--orange);font-size:11px}
  .calc-grid{display:grid;grid-template-columns:1fr 1fr;gap:7px;margin-top:12px}
  .field{height:20px;border:1px solid var(--line);background:var(--white);font-size:6.5px;color:#999;padding:6px 5px}
  .calc-label{font-size:7px;margin-top:12px;color:var(--grey)}
  .calc-choice{display:flex;gap:6px;margin-top:4px}
  .calc-choice .field{width:34px;height:16px;padding:4px 5px}
  .calc-submit{margin-top:12px}

  .services{position:absolute;left:0;top:630px;width:744px;height:250px;
    background:linear-gradient(180deg,var(--orange-light),var(--orange) 60%,var(--orange-deep))}
  .services .section-title{color:var(--white);text-align:center;margin-top:28px}
  .service-list{position:absolute;left:62px;top:100px;width:612px;display:flex;justify-content:space-between}
  .service{width:193px}
  .service-photo{height:100px;box-shadow:0 2px 5px rgba(0,0,0,.25)}
  .service:nth-child(1) .service-photo{background:linear-gradient(135deg,#9b4a36,#c98a6a 60%,#6f7a80)}
  .service:nth-child(2) .service-photo{background:linear-gradient(135deg,#a9b6c1,#b36d4c 55%,#e2ded6)}
  .service:nth-child(3) .service-photo{background:linear-gradient(135deg,#8c959c,#cfd4d6 55%,#5b6066)}
  .service h4{color:var(--white);font-weight:300;font-size:14px;margin-top:16px;white-space:nowrap}

  .testimonial{position:absolute;left:62px;top:880px;width:612px;height:245px}
  .testimonial .section-title{text-align:center;margin-top:36px}
  .slider-arrows{position:absolute;right:0;top:42px;display:flex;gap:14px}
  .client-photo{position:absolute;left:0;top:120px;width:78px;height:78px;border-radius:50%;
    background:linear-gradient(160deg,#d9c7b4,#8a6f58)}
  .quote-mark{position:absolute;left:112px;top:112px;font-size:44px;color:#ccc;font-weight:700;line-height:1}
  .quote-text{position:absolute;left:112px;top:152px;width:480px;font-size:6.8px;line-height:1.6;color:var(--grey)}
  .client-name{position:absolute;left:112px;top:180px;font-size:7px;color:var(--orange)}

  .site-footer{position:absolute;left:0;top:1132px;width:744px;height:68px;background:var(--footer);color:#ccc}
  .footer-nav{position:absolute;left:62px;top:22px;display:flex;gap:16px}
  .footer-nav a{font-size:6px;color:#ccc;text-decoration:none}
  .copyright{position:absolute;left:62px;top:40px;font-size:5.5px;color:#999}
  .social{position:absolute;right:80px;top:22px;display:flex;gap:6px}
  .social span{width:14px;height:14px;border-radius:50%;background:#ddd}
  .to-top{position:absolute;right:58px;top:25px}
</style>
</head>
<body>
  <header class="site-header">
    <div class="brand"><span class="brand-mark"></span>Rowen Build</div>
    <div class="contact-line">0400 555 019 &nbsp;|&nbsp; hello@rowenhq.example</div>
    <nav class="main-nav">
      <a href="#">HOME</a><a href="#">ABOUT US</a><a href="#">SERVICES</a><a href="#">PROJECTS</a><a href="#">TESTIMONIALS</a><a href="#">CONTACT US</a>
    </nav>
  </header>

  <section class="hero" role="img" aria-label="Builders in hard hats reviewing plans on site">
    <div class="hero-arrow prev"><svg width="6" height="10" viewBox="0 0 6 10"><path d="M5 1 1 5l4 4" stroke="#fff" fill="none" stroke-width="1.5"/></svg></div>
    <div class="hero-arrow next"><svg width="6" height="10" viewBox="0 0 6 10"><path d="M1 1l4 4-4 4" stroke="#fff" fill="none" stroke-width="1.5"/></svg></div>
    <div class="hero-caption">
      <h2>Building Advice</h2>
      <p>Do you need building advice, or simply someone to help you through the labyrinth of the building industry?</p>
    </div>
  </section>

  <section class="about">
    <h2 class="section-title">ABOUT US</h2>
    <div class="about-photo" role="img" aria-label="House frame under construction"></div>
    <div class="about-text">
      <p>Rowen Build – Operations Manager and Business Principal – brings many years of experience in the building trade across all areas of light commercial, medium density and residential construction, and has been involved from all sides of the complex process that is the building industry.</p>
      <p>Commencing as an apprentice plumber in 1995, then carrying on through estimating and site management roles through to 2005 and later years, it was an excellent grounding to gain a thorough understanding of the industry. Working on residential.</p>
    </div>
    <span class="btn read-more">READ MORE</span>

    <aside class="calculator">
      <h3>PROJECT CALCULATOR</h3>
      <div class="calc-grid">
        <div class="field">Sq ft</div><div class="field">Storeys</div>
        <div class="field">Type</div><div class="field">Rooms</div>
      </div>
      <div class="calc-label">Basement</div>
      <div class="calc-choice"><div class="field">Yes</div><div class="field">No</div></div>
      <span class="btn calc-submit">GET ESTIMATE</span>
    </aside>
  </section>

  <section class="services">
    <h2 class="section-title">WHAT WE DO</h2>
    <div class="service-list">
      <div class="service"><div class="service-photo" role="img" aria-label="Brick home built on a tight site"></div><h4>TIGHT SITE</h4></div>
      <div class="service"><div class="service-photo" role="img" aria-label="Renovated single storey home"></div><h4>STOREY ALTERATIONS</h4></div>
      <div class="service"><div class="service-photo" role="img" aria-label="Weatherboard second storey addition"></div><h4>STOREY ADDITIONS</h4></div>
    </div>
  </section>

  <section class="testimonial">
    <h2 class="section-title">CUSTOMER TESTIMONIAL</h2>
    <div class="slider-arrows">
      <svg width="8" height="12" viewBox="0 0 8 12"><path d="M6 1 1 6l5 5" stroke="#999" fill="none" stroke-width="1.5"/></svg>
      <svg width="8" height="12" viewBox="0 0 8 12"><path d="M2 1l5 5-5 5" stroke="#999" fill="none" stroke-width="1.5"/></svg>
    </div>
    <div class="client-photo" role="img" aria-label="Portrait of a happy client"></div>
    <div class="quote-mark">&ldquo;</div>
    <p class="quote-text">Working with the team was a pleasure from start to finish. Clear advice, honest pricing and a build we are proud of. We would happily recommend them to anyone.</p>
    <div class="client-name">Jane Doe</div>
  </section>

  <footer class="site-footer">
    <nav class="footer-nav">
      <a href="#">HOME</a><a href="#">ABOUT US</a><a href="#">SERVICES</a><a href="#">PROJECTS</a><a href="#">TESTIMONIALS</a><a href="#">CONTACT US</a>
    </nav>
    <div class="copyright">© 2015 ROWENHQ. ALL RIGHTS RESERVED.</div>
    <div class="social"><span></span><span></span><span></span></div>
    <svg class="to-top" width="8" height="8" viewBox="0 0 8 8"><path d="M1 6l3-4 3 4" stroke="#ccc" fill="none" stroke-width="1.3"/></svg>
  </footer>
</body>
</html>
```